Designer Instructions – Updated Referral Program Flyer

(Based on the mock-up in “Brief Layout and Instructions.pdf”)

OVERALL STYLE + LAYOUT

Maintain the same general layout, structure, and flow as the mock-up flyer (front and back).

This is an update of an older flyer, not a full redesign — keep the same sections, proportions, and overall visual feel, but with cleaner, more modern design improvements.

The final flyer should look clean, bold, professional, and high-impact, geared toward realtors, property managers, and contractors who refer work.

FRONT SIDE INSTRUCTIONS
1. Header Section

Remove the Rebuild Harbor Crest logo from the top banner.
(Shown on page 1 of the PDF)

2. Main Headline

Keep the same three-line structure:
EARN
UNLIMITED
CASH

Center it, maximize impact, and increase the font size of CASH so all three words match in importance.

Make the headline bold, clean, and the main focal point.

3. Cash Incentive Box

Keep the "$500 minimum OR 10% per referral" box, but upgrade the graphics to look sharper and more modern.

Ensure the wording matches exactly what’s in the mock-up.

4. Premier Partner Program Ribbon

Clean up and modernize the "PREMIER PARTNER PROGRAM" bar while keeping the same position and structure.

Ensure the checkmark badge remains crisp and professional.

5. Supporting Icons Section

Keep the four icons/benefit boxes (Guaranteed Payout, Free Evaluations, Affordable Solutions, Industry Leaders) in the same order.

Update the icons to cleaner, more modern styles — but maintain the same meanings.

Improve alignment and spacing for sharper visual consistency.

6. Remove Icons in Contact Area

At the bottom (“CALL TEXT OR BOOK ONLINE 858-471-6093 BrightlaneRenovate.com”), remove the phone and internet icons, as noted on page 2 of the PDF.

7. Replace All Images

I (Dorian) will provide all updated stock images separately via email.

Replace the flood/water-damage imagery and roof leak with the new images I send.

Keep image placement and proportions the same as the mock-up.

BACK SIDE INSTRUCTIONS
1. Header Image + “REFER / EARN” Section

Maintain the same large split-image layout (“The more you refer, the more you earn”).

Replace all background imagery with the new assets I will send.

Keep the CASH FLOW image section but modernize the type and spacing.

2. “HOW IT WORKS” Section

Preserve the three-column layout:

Refer Flood, Water & Mold Damage

We Take Care of Everything (evaluations/insurance)

Get Paid to Share

Update images, tighten spacing, and use modern iconography.

3. Remove Phone/Internet Icons

Same as the front side — remove small communication icons and keep only the text/number/URL.

4. Bottom Contact Bar

Keep the blue bar, same wording, same layout — just modernize the style if needed for clarity.

5. Replace All Back-Side Images

Again, I will email you the image assets.

Keep the layout EXACT — just update with higher-quality photos and improved design.

TEXT CONTENT (Keep as-is unless spacing adjustments needed)

All text shown in the PDF should remain exactly the same unless spacing or visual balance requires minor adjustments.
Example from page 3:

“REFER FLOOD, MOLD & CONSTRUCTION JOBS”

“We Schedule a Free Estimate. If Approved, You Get Paid.”

“Everybody Benefits From Referrals”

Everything stays, just refreshed and visually improved.

DESIGN GOALS

Flyer should look high-end and trustworthy, not salesy.

Consistent color theme: blues, whites, yellows, same palette as original.

Use bold, modern fonts with strong readability.

Ensure all headlines pop and all benefit boxes are clean, well-aligned, and evenly spaced.

The final result should feel like a premium referral program flyer for a top-tier restoration/remodel company.

FILES I WILL PROVIDE

I will send the designer:

All replacement stock photos

Any updated logos (if needed)

Original high-resolution version of the mock-up (if available)

Any additional icons preferred

Colors
0054AA
0677BA
7BADD7
CADEEF
E8F1F8

Requirements
Must have
• Designer Instructions – Updated Referral Program Flyer (Based on the mock-up in “Brief Layout and Instructions.pdf”) OVERALL STYLE + LAYOUT Maintain the same general layout, structure, and flow as the mock-up flyer (front and back). This is an update of an older flyer, not a full redesign — keep the same sections, proportions, and overall visual feel, but with cleaner, more modern design improvements. The final flyer should look clean, bold, professional, and high-impact, geared toward realtors, property managers, and contractors who refer work. FRONT SIDE INSTRUCTIONS 1. Header Section Remove the Rebuild Harbor Crest logo from the top banner. (Shown on page 1 of the PDF) 2. Main Headline Keep the same three-line structure: EARN UNLIMITED CASH Center it, maximize impact, and increase the font size of CASH so all three words match in importance. Make the headline bold, clean, and the main focal point. 3. Cash Incentive Box Keep the "$500 minimum OR 10% per referral" box, but upgrade the graphics to look sharper and more modern. Ensure the wording matches exactly what’s in the mock-up. 4. Premier Partner Program Ribbon Clean up and modernize the "PREMIER PARTNER PROGRAM" bar while keeping the same position and structure. Ensure the checkmark badge remains crisp and professional. 5. Supporting Icons Section Keep the four icons/benefit boxes (Guaranteed Payout, Free Evaluations, Affordable Solutions, Industry Leaders) in the same order. Update the icons to cleaner, more modern styles — but maintain the same meanings. Improve alignment and spacing for sharper visual consistency. 6. Remove Icons in Contact Area At the bottom (“CALL TEXT OR BOOK ONLINE 858-471-6093 BrightlaneRenovate.com”), remove the phone and internet icons, as noted on page 2 of the PDF. 7. Replace All Images I (Dorian) will provide all updated stock images separately via email. Replace the flood/water-damage imagery and roof leak with the new images I send. Keep image placement and proportions the same as the mock-up. BACK SIDE INSTRUCTIONS 1. Header Image + “REFER / EARN” Section Maintain the same large split-image layout (“The more you refer, the more you earn”). Replace all background imagery with the new assets I will send. Keep the CASH FLOW image section but modernize the type and spacing. 2. “HOW IT WORKS” Section Preserve the three-column layout: Refer Flood, Water & Mold Damage We Take Care of Everything (evaluations/insurance) Get Paid to Share Update images, tighten spacing, and use modern iconography. 3. Remove Phone/Internet Icons Same as the front side — remove small communication icons and keep only the text/number/URL. 4. Bottom Contact Bar Keep the blue bar, same wording, same layout — just modernize the style if needed for clarity. 5. Replace All Back-Side Images Again, I will email you the image assets. Keep the layout EXACT — just update with higher-quality photos and improved design. TEXT CONTENT (Keep as-is unless spacing adjustments needed) All text shown in the PDF should remain exactly the same unless spacing or visual balance requires minor adjustments. Example from page 3: “REFER FLOOD, MOLD & CONSTRUCTION JOBS” “We Schedule a Free Estimate. If Approved, You Get Paid.” “Everybody Benefits From Referrals” Everything stays, just refreshed and visually improved. DESIGN GOALS Flyer should look high-end and trustworthy, not salesy. Consistent color theme: blues, whites, yellows, same palette as original. Use bold, modern fonts with strong readability. Ensure all headlines pop and all benefit boxes are clean, well-aligned, and evenly spaced. The final result should feel like a premium referral program flyer for a top-tier restoration/remodel company. FILES I WILL PROVIDE I will send the designer: All replacement stock photos Any updated logos (if needed) Original high-resolution version of the mock-up (if available) Any additional icons preferred

```html
<!DOCTYPE html>
<html lang="en">
<head>
<meta charset="utf-8">
<title>Premier Partner Referral Flyer</title>
<link rel="stylesheet" href="https://fonts.googleapis.com/css2?family=Montserrat:wght@600;700;800;900&display=swap">
<style>
  :root {
    --navy: #1a3577;
    --navy-deep: #152c66;
    --blue: #1f6fc9;
    --blue-light: #3f8fe0;
    --red: #d42027;
    --yellow: #ffe500;
    --white: #ffffff;
    --silver: #c9cbce;
    --silver-light: #f2f2f3;
    --photo-dark: #6d6f73;
    --photo-light: #d9dadc;
  }
  html, body { margin: 0; padding: 0; overflow: hidden; background: #ffffff; }
  .flyer { display: block; width: 1200px; height: 800px; }
  .flyer text { font-family: 'Montserrat', sans-serif; }
  .headline-earn { font-weight: 900; fill: var(--yellow); }
  .headline-white { font-weight: 900; fill: var(--white); }
  .band-text { font-weight: 800; fill: var(--navy); }
  .offer-big { font-weight: 900; fill: var(--white); }
  .offer-small { font-weight: 800; fill: var(--white); }
  .offer-or { font-weight: 900; fill: var(--navy); }
  .ribbon-premier { font-weight: 700; fill: var(--red); }
  .ribbon-word { font-weight: 900; fill: var(--white); }
  .tagline { font-weight: 900; fill: var(--white); }
  .benefit-title { font-weight: 800; fill: var(--white); }
  .benefit-body { font-weight: 700; fill: var(--navy); }
  .slogan { font-weight: 900; fill: var(--white); }
  .slogan .accent { fill: var(--red); }
  .contact-label { font-weight: 800; fill: var(--white); }
  .contact-label .light { font-weight: 600; }
  .contact-details { font-weight: 600; fill: var(--white); }
</style>
</head>
<body>
<svg class="flyer" viewBox="0 0 1200 800" xmlns="http://www.w3.org/2000/svg">
  <defs>
    <linearGradient id="photoTone" x1="0" y1="0" x2="1" y2="1">
      <stop offset="0" stop-color="var(--photo-light)"/>
      <stop offset="0.5" stop-color="var(--photo-dark)"/>
      <stop offset="1" stop-color="var(--photo-light)"/>
    </linearGradient>
    <linearGradient id="waterTone" x1="0" y1="0" x2="1" y2="1">
      <stop offset="0" stop-color="#1866c0"/>
      <stop offset="0.5" stop-color="var(--blue-light)"/>
      <stop offset="1" stop-color="#1a68c2"/>
    </linearGradient>
    <linearGradient id="silverTone" x1="0" y1="0" x2="0" y2="1">
      <stop offset="0" stop-color="var(--silver)"/>
      <stop offset="0.5" stop-color="var(--silver-light)"/>
      <stop offset="1" stop-color="var(--silver)"/>
    </linearGradient>
    <linearGradient id="shieldTone" x1="0" y1="0" x2="1" y2="0">
      <stop offset="0" stop-color="#b9bbbe"/>
      <stop offset="0.5" stop-color="#ffffff"/>
      <stop offset="1" stop-color="#b9bbbe"/>
    </linearGradient>
  </defs>

  <!-- Top section -->
  <rect class="hero-panel" x="0" y="0" width="1200" height="386" fill="var(--navy)"/>
  <polygon class="photo-frame" points="663,0 1200,0 1200,386 684,386 597,167" fill="url(#silverTone)"/>
  <polygon class="hero-photo" role="img" aria-label="Photo of a leaking white drain pipe under a sink" points="672,0 1200,0 1200,386 693,386 608,167" fill="url(#photoTone)"/>
  <g class="emergency-badge">
    <rect x="962" y="0" width="146" height="50" fill="var(--white)"/>
    <circle cx="1035" cy="92" r="70" fill="var(--white)"/>
    <circle cx="1035" cy="92" r="62" fill="var(--red)"/>
  </g>

  <g class="headline">
    <text class="headline-earn" x="122" y="148" font-size="132" textLength="374" lengthAdjust="spacingAndGlyphs">EARN</text>
    <text class="headline-white" x="124" y="201" font-size="57" textLength="358" lengthAdjust="spacingAndGlyphs">UNLIMITED</text>
    <text class="headline-white" x="107" y="306" font-size="134" textLength="386" lengthAdjust="spacingAndGlyphs">CASH</text>
  </g>

  <polygon class="yellow-band" points="0,325 654,325 672,366 0,366" fill="var(--yellow)"/>
  <text class="band-text" x="110" y="356" font-size="31" textLength="457" lengthAdjust="spacingAndGlyphs">GET PAID TO REFER A FLOOD</text>

  <!-- Lower section -->
  <rect class="water-panel" role="img" aria-label="Blue background of water droplets" x="0" y="386" width="1200" height="414" fill="url(#waterTone)"/>

  <g class="offer-box">
    <rect x="81" y="402" width="563" height="92" rx="12" fill="var(--red)"/>
    <text class="offer-big" x="104" y="455" font-size="56" textLength="128" lengthAdjust="spacingAndGlyphs">$500</text>
    <text class="offer-small" x="107" y="481" font-size="24" textLength="122" lengthAdjust="spacingAndGlyphs">MINIMUM</text>
    <circle cx="297" cy="448" r="46" fill="var(--white)"/>
    <text class="offer-or" x="297" y="460" font-size="33" text-anchor="middle">OR</text>
    <text class="offer-big" x="357" y="470" font-size="66" textLength="130" lengthAdjust="spacingAndGlyphs">10%</text>
    <text class="offer-small" x="492" y="447" font-size="23">PER</text>
    <text class="offer-small" x="492" y="470" font-size="23" textLength="126" lengthAdjust="spacingAndGlyphs">REFERRAL</text>
  </g>

  <g class="partner-ribbon">
    <rect x="656" y="401" width="469" height="94" rx="12" fill="var(--navy)"/>
    <path d="M668,429 H890 V495 H668 A12,12 0 0 1 656,483 V429 Z" fill="var(--red)"/>
    <path d="M668,401 H1113 A12,12 0 0 1 1125,413 V429 H656 V413 A12,12 0 0 1 668,401 Z" fill="url(#silverTone)"/>
    <text class="ribbon-premier" x="891" y="424" font-size="21" text-anchor="middle" letter-spacing="22">PREMIER</text>
    <text class="ribbon-word" x="677" y="475" font-size="32" textLength="167" lengthAdjust="spacingAndGlyphs">PARTNER</text>
    <text class="ribbon-word" x="932" y="475" font-size="32" textLength="179" lengthAdjust="spacingAndGlyphs">PROGRAM</text>
    <path class="check-shield" d="M862,438 Q890,430 918,438 V466 Q918,486 890,497 Q862,486 862,466 Z" fill="url(#shieldTone)"/>
    <path d="M874,460 L886,472 L908,448" fill="none" stroke="var(--red)" stroke-width="8" stroke-linecap="round" stroke-linejoin="round"/>
  </g>

  <text class="tagline" x="87" y="544" font-size="46" textLength="1031" lengthAdjust="spacingAndGlyphs">PARTNER WITH US &amp; EVERYBODY WINS!</text>

  <!-- Benefit boxes -->
  <g class="benefit benefit-refer">
    <rect x="81" y="559" width="234" height="111" rx="10" fill="var(--navy)"/>
    <rect x="84" y="609" width="228" height="58" rx="8" fill="url(#silverTone)"/>
    <text class="benefit-title" x="198" y="580" font-size="18" text-anchor="middle">EVERYONE</text>
    <text class="benefit-title" x="198" y="600" font-size="18" text-anchor="middle">CAN REFER</text>
    <text class="benefit-body" x="104" y="627" font-size="12.5">Plumbers, Contractors,</text>
    <text class="benefit-body" x="104" y="642" font-size="12.5">Agents, Roofers</text>
    <text class="benefit-body" x="104" y="657" font-size="12.5">&amp; Friends</text>
    <circle cx="287" cy="638" r="19" fill="var(--white)" stroke="var(--red)" stroke-width="4"/>
    <path d="M278,638 L285,645 L297,632" fill="none" stroke="var(--red)" stroke-width="5" stroke-linecap="round" stroke-linejoin="round"/>
  </g>

  <g class="benefit benefit-insurance">
    <rect x="351" y="559" width="234" height="111" rx="10" fill="var(--navy)"/>
    <rect x="354" y="609" width="228" height="58" rx="8" fill="url(#silverTone)"/>
    <text class="benefit-title" x="468" y="580" font-size="18" text-anchor="middle">INSURANCE</text>
    <text class="benefit-title" x="468" y="600" font-size="18" text-anchor="middle">SPECIALISTS</text>
    <text class="benefit-body" x="376" y="627" font-size="12.5">We Use Claimwise To</text>
    <text class="benefit-body" x="376" y="642" font-size="12.5">Secure Clients The</text>
    <text class="benefit-body" x="376" y="657" font-size="12.5">Maximum Payout</text>
    <rect x="537" y="619" width="30" height="41" rx="4" fill="var(--white)" stroke="var(--red)" stroke-width="3"/>
    <path d="M543,630 H561 M543,637 H561 M543,644 H556" stroke="var(--red)" stroke-width="3"/>
    <circle cx="566" cy="657" r="9" fill="var(--red)"/>
  </g>

  <g class="benefit benefit-affordable">
    <rect x="620" y="559" width="233" height="111" rx="10" fill="var(--navy)"/>
    <rect x="623" y="609" width="227" height="58" rx="8" fill="url(#silverTone)"/>
    <text class="benefit-title" x="736" y="580" font-size="18" text-anchor="middle">AFFORDABLE</text>
    <text class="benefit-title" x="736" y="600" font-size="18" text-anchor="middle">SOLUTIONS</text>
    <text class="benefit-body" x="643" y="627" font-size="12.5">We Offer Lowest Out</text>
    <text class="benefit-body" x="643" y="642" font-size="12.5">of Pocket Costs for</text>
    <text class="benefit-body" x="643" y="657" font-size="12.5">Your Customers</text>
    <path d="M792,622 Q812,612 838,616" fill="none" stroke="var(--red)" stroke-width="4" stroke-linecap="round"/>
    <circle cx="815" cy="638" r="10" fill="none" stroke="var(--red)" stroke-width="3"/>
    <path d="M788,656 Q810,664 832,650" fill="none" stroke="var(--red)" stroke-width="4" stroke-linecap="round"/>
  </g>

  <g class="benefit benefit-leaders">
    <rect x="890" y="559" width="234" height="111" rx="10" fill="var(--navy)"/>
    <rect x="893" y="609" width="228" height="58" rx="8" fill="url(#silverTone)"/>
    <text class="benefit-title" x="1007" y="580" font-size="18" text-anchor="middle">INDUSTRY</text>
    <text class="benefit-title" x="1007" y="600" font-size="18" text-anchor="middle">LEADERS</text>
    <text class="benefit-body" x="906" y="627" font-size="12.5">We are RSCB Certified</text>
    <text class="benefit-body" x="906" y="642" font-size="12.5">Licensed General</text>
    <text class="benefit-body" x="906" y="657" font-size="12.5">Contractors</text>
    <circle cx="1092" cy="626" r="7" fill="var(--white)" stroke="var(--red)" stroke-width="3"/>
    <path d="M1072,662 V650 Q1072,638 1092,638 Q1112,638 1112,650 V662 Z" fill="var(--white)" stroke="var(--red)" stroke-width="3"/>
  </g>

  <text class="slogan" x="81" y="709" font-size="38" textLength="1045" lengthAdjust="spacingAndGlyphs">SEND <tspan class="accent">REFERRALS.</tspan> GET <tspan class="accent">PAID.</tspan> GROW <tspan class="accent">YOUR BUSINESS.</tspan></text>

  <!-- Contact bar -->
  <polygon class="contact-bar" points="0,722 508,722 550,800 0,800" fill="var(--navy)"/>
  <text class="contact-label" x="79" y="762" font-size="29" textLength="424" lengthAdjust="spacingAndGlyphs">CALL, TEXT <tspan class="light">OR</tspan> BOOK ONLINE</text>
  <text class="contact-details" x="536" y="762" font-size="30" textLength="592" lengthAdjust="spacingAndGlyphs">858·471·6093 • BrightlaneRenovate.com</text>
</svg>
</body>
</html>
```